Kor'v Meridell Travel

We need a sleek, professional, inviting card to elicit global travel for the experienced and professional traveler. Royal blue, black and silver. (perhaps the wording could be silver with black shadow?-get creative) Maybe a watermark on the front and the full raised logo on the back.
We want a stylish and modern card, but professional.

```html
<!DOCTYPE html>
<html lang="en">
<head>
<meta charset="utf-8">
<title>Kor'v Meridell Travel — Business Card</title>
<link rel="stylesheet" href="https://fonts.googleapis.com/css2?family=Open+Sans:ital,wght@0,400;0,700;0,800;1,400&display=swap">
<style>
  :root {
    --bg: #2a2a2c;
    --card: #1d1d1f;
    --blue: #1fa3e0;
    --green: #8cc63f;
    --silver: #c9c9cc;
    --silver-dark: #6d6d72;
    --text-grey: #b8b8bb;
  }
  * { margin: 0; padding: 0; box-sizing: border-box; }
  html, body {
    width: 1200px; height: 900px; overflow: hidden;
    background: var(--bg);
    font-family: "Open Sans", Arial, sans-serif;
  }
  .canvas {
    width: 1200px; height: 900px;
    display: flex; flex-direction: column; align-items: center; justify-content: center;
    gap: 40px;
  }
  .card {
    position: relative;
    width: 700px; height: 400px;
    background: var(--card);
    border-bottom: 10px solid var(--blue);
    box-shadow: 0 14px 30px rgba(0,0,0,0.45);
    overflow: hidden;
  }
  /* front */
  .brand {
    position: absolute; left: 70px; top: 70px;
    display: flex; align-items: center; gap: 12px;
  }
  .brand-dot { width: 14px; height: 14px; border-radius: 50%; background: var(--blue); }
  .brand-name {
    font-weight: 800; font-size: 30px; letter-spacing: 1px;
    color: var(--blue); text-transform: uppercase;
  }
  .divider {
    position: absolute; left: 150px; right: 40px; top: 205px;
    height: 2px; background: var(--blue);
  }
  .contact-list {
    position: absolute; left: 56px; top: 228px;
    list-style: none;
  }
  .contact-list li {
    display: flex; align-items: center; gap: 10px;
    font-size: 17px; color: var(--text-grey); line-height: 30px;
  }
  .contact-list svg { width: 14px; height: 14px; fill: var(--green); flex: none; }
  .person {
    position: absolute; right: 50px; top: 120px; text-align: right;
  }
  .person-name {
    font-weight: 800; font-style: italic; font-size: 26px; color: var(--blue);
    text-transform: uppercase; letter-spacing: 0.5px;
  }
  .person-title { font-size: 18px; color: var(--text-grey); }
  .address {
    position: absolute; right: 50px; top: 228px; text-align: right;
    font-size: 18px; color: var(--text-grey); line-height: 28px;
  }
  /* back */
  .card-back { display: flex; align-items: center; justify-content: center; }
  .back-name {
    font-weight: 800; font-size: 44px; letter-spacing: 2px;
    color: var(--silver-dark); text-transform: uppercase;
  }
</style>
</head>
<body>
<main class="canvas">
  <section class="card card-front">
    <div class="brand">
      <span class="brand-dot"></span>
      <span class="brand-name">Kor'v Meridell Travel</span>
    </div>

    <div class="person">
      <p class="person-name">Dario Fenwick</p>
      <p class="person-title">President</p>
    </div>

    <div class="divider"></div>

    <ul class="contact-list">
      <li>
        <svg viewBox="0 0 16 16"><path d="M3.6 1.2 6 3.6 4.7 5.6c.9 2 2.5 3.7 4.6 4.7L11.3 9l2.5 2.4-1.4 2.6C6.6 13.6 2.4 9.4 1 3.6z"/></svg>
        949-555-0172
      </li>
      <li>
        <svg viewBox="0 0 16 16"><path d="M1 3h14v10H1zM1.8 3.8 8 8.6l6.2-4.8" stroke="#1d1d1f" stroke-width="1"/></svg>
        info@korvmeridell.com
      </li>
      <li>
        <svg viewBox="0 0 16 16"><circle cx="8" cy="8" r="7"/><path d="M1 8h14M8 1c-3 3-3 11 0 14M8 1c3 3 3 11 0 14" stroke="#1d1d1f" stroke-width="1" fill="none"/></svg>
        www.korvmeridell.com
      </li>
    </ul>

    <p class="address">31870 Harborlight Way<br>Seacliff CA 92600</p>
  </section>

  <section class="card card-back">
    <span class="back-name">Kor'v Meridell Travel</span>
  </section>
</main>
</body>
</html>
```